Rebrand stationary with recently completed logo design

Need new business cards, thank you cards, letterhead, envelopes and presentation folders. The designs will be sent to a separate production firm so I need the files to be print ready.

My contact info
Reko Haliburn

Office 604-318-5047
Fax 604-371-8054

Email reko@glazemark.ca
website www.glazemark.ca

315-14720 62nd Avenue,
Langley, BC, V2K 3R8

Target Market(s)

Homeowners, businesses and contractors

Industry/Entity Type

Business

Font styles to use
Sans Serif

Colors
34a7d7

Requirements
Must have
• Like to have one side of the business card a solid color with the logo in all white. The side with all the text to be a white background
• I find the current blue on the front of the card with the white logo too dark.
Should not have
• Gradient colors

```html
<!DOCTYPE html>
<html lang="en">
<head>
<meta charset="utf-8">
<title>Glazemark Business Card</title>
<link rel="stylesheet" href="https://fonts.googleapis.com/css2?family=Open+Sans:wght@400;600;700&display=swap">
<style>
  :root {
    --backdrop: #2b2b2c;
    --card-white: #f3f3f3;
    --brand-blue: #34a7d7;
    --slate: #3e4b55;
    --text-grey: #4e4e4e;
    --divider: #c9c9c9;
    --white: #ffffff;
  }
  html, body {
    margin: 0;
    padding: 0;
    width: 1200px;
    height: 960px;
    overflow: hidden;
    background: var(--backdrop);
    font-family: "Open Sans", Arial, sans-serif;
  }
  .canvas {
    position: relative;
    width: 1200px;
    height: 960px;
  }
  .card {
    position: absolute;
    width: 600px;
    height: 342px;
    box-shadow: 0 3px 10px rgba(0,0,0,0.45);
  }
  .card-front {
    left: 302px;
    top: 129px;
    background: var(--card-white);
  }
  .card-back {
    left: 299px;
    top: 488px;
    background: var(--brand-blue);
  }

  /* front: brand lockup */
  .brand-lockup {
    position: absolute;
    left: 128px;
    top: 86px;
    display: flex;
    align-items: center;
    gap: 18px;
  }
  .brand-square {
    width: 52px;
    height: 52px;
    background: var(--brand-blue);
  }
  .brand-name {
    font-size: 46px;
    font-weight: 600;
    color: var(--slate);
    letter-spacing: 1px;
    line-height: 1;
  }

  /* front: contact block */
  .holder {
    position: absolute;
    right: 315px;
    top: 218px;
    text-align: right;
  }
  .holder-name {
    font-size: 19px;
    font-weight: 600;
    color: var(--brand-blue);
    line-height: 1.2;
    margin-bottom: 4px;
  }
  .holder-address {
    font-size: 13px;
    color: var(--text-grey);
    line-height: 19px;
  }
  .contact-divider {
    position: absolute;
    left: 302px;
    top: 223px;
    width: 1px;
    height: 61px;
    background: var(--divider);
  }
  .contact-list {
    position: absolute;
    left: 320px;
    top: 226px;
    margin: 0;
    padding: 0;
    list-style: none;
  }
  .contact-list li {
    display: flex;
    align-items: center;
    gap: 7px;
    font-size: 13px;
    color: var(--text-grey);
    line-height: 18.5px;
    white-space: nowrap;
  }
  .contact-icon {
    width: 13px;
    height: 12px;
    color: var(--brand-blue);
    fill: currentColor;
    flex: none;
  }
  .contact-icon .paper {
    fill: var(--card-white);
  }
  .contact-icon .envelope {
    fill: none;
    stroke: currentColor;
    stroke-width: 2;
  }

  /* back */
  .back-name {
    position: absolute;
    left: 0;
    right: 0;
    top: 130px;
    text-align: center;
    font-size: 44px;
    font-weight: 600;
    color: var(--white);
    letter-spacing: 1px;
  }
  .web-address {
    position: absolute;
    left: 0;
    right: 0;
    top: 286px;
    text-align: center;
    font-size: 13px;
    letter-spacing: 3px;
    color: var(--white);
  }
  .web-address strong {
    font-weight: 700;
  }
</style>
</head>
<body>
<main class="canvas">

  <section class="card card-front">
    <div class="brand-lockup">
      <div class="brand-square"></div>
      <div class="brand-name">GLAZEMARK</div>
    </div>

    <div class="holder">
      <div class="holder-name">Reko Haliburn</div>
      <div class="holder-address">315-14720 62nd Avenue<br>Langley, BC, V2K 3R8</div>
    </div>

    <div class="contact-divider"></div>

    <ul class="contact-list">
      <li>
        <svg class="contact-icon" viewBox="0 0 24 24" aria-hidden="true">
          <path d="M6.6 10.8c1.4 2.8 3.8 5.1 6.6 6.6l2.2-2.2c.3-.3.7-.4 1-.2 1.1.4 2.3.6 3.6.6.6 0 1 .4 1 1V20c0 .6-.4 1-1 1C10.6 21 3 13.4 3 4c0-.6.4-1 1-1h3.5c.6 0 1 .4 1 1 0 1.3.2 2.5.6 3.6.1.3 0 .7-.2 1L6.6 10.8z"/>
        </svg>
        604-318-5047
      </li>
      <li>
        <svg class="contact-icon" viewBox="0 0 24 22" aria-hidden="true">
          <rect x="6" y="1" width="12" height="6"/>
          <rect x="1" y="8" width="22" height="9" rx="2"/>
          <rect class="paper" x="6" y="14" width="12" height="7"/>
          <rect x="7.5" y="15.5" width="9" height="5"/>
        </svg>
        604-371-8054
      </li>
      <li>
        <svg class="contact-icon" viewBox="0 0 24 18" aria-hidden="true">
          <path class="envelope" d="M1 2h22v14H1z M2.5 3.5 12 10.5 21.5 3.5"/>
        </svg>
        reko@glazemark.ca
      </li>
    </ul>
  </section>

  <section class="card card-back">
    <div class="back-name">GLAZEMARK</div>
    <div class="web-address">www.<strong>glazemark</strong>.ca</div>
  </section>

</main>
</body>
</html>
```